QRTV Membership Web Design Project

We need a website design for QRTV membership. We need something different from what we currently have. See what we currently have: http://www.qorvatu.org/klt4/

Make provision for where members bushiness can be advertised.
Updates

We need a box for advertising members projects/business.

Make provision for where members bushiness / products can be advertised.

Target Market(s)

For members of QRTV and Intending members. Membership is for married men only.

Requirements
Must have
• Make provision for where members bushiness can be advertised.

You are to redesign: http://www.qorvatu.org/klt4/

```html
<!DOCTYPE html>
<html lang="en">
<head>
<meta charset="utf-8">
<title>QRTV – Heralds of Grace International Fellowship</title>
<link rel="stylesheet" href="https://fonts.googleapis.com/css2?family=PT+Sans+Narrow:wght@400;700&family=Arimo:wght@400&display=swap">
<style>
:root{
  --green:#94c11f;
  --green-dark:#6f9a12;
  --blue:#3a73b8;
  --orange:#fbb21b;
  --nav-top:#3a3a3a;
  --nav-bottom:#0c0c0c;
  --text:#1b1b1b;
  --muted:#6e6e6e;
  --grey-panel:#5f5f5f;
  --footer:#666666;
  --white:#ffffff;
}
*{box-sizing:border-box;margin:0;padding:0}
html,body{width:1011px;height:1200px;overflow:hidden;background:var(--white)}
body{position:relative;font-family:"Arimo",Arial,sans-serif;color:var(--text)}
.brand{position:absolute;left:12px;top:18px;display:flex;align-items:center;gap:10px}
.brand-mark{width:62px;height:62px;border-radius:50%;background:var(--green)}
.brand-name{font-family:"PT Sans Narrow",sans-serif;font-weight:700;font-size:26px;color:#2f5f9e;line-height:1}
.tagline{position:absolute;left:90px;top:66px;font-family:"PT Sans Narrow",sans-serif;font-size:19px;color:var(--muted);letter-spacing:1px;text-transform:uppercase}
.search{position:absolute;left:700px;top:20px;width:306px;height:70px;background:var(--green);border-radius:12px}
.search-field{position:absolute;left:12px;top:17px;width:190px;height:38px;background:#f1f1f1;border-radius:4px}
.search-btn{position:absolute;left:206px;top:17px;width:88px;height:38px;background:linear-gradient(#fff,#dcdcdc);border-radius:4px;font-size:15px;color:#333;display:flex;align-items:center;justify-content:center}
.nav{position:absolute;left:3px;top:105px;width:1003px;height:59px;background:linear-gradient(var(--nav-top),var(--nav-bottom));border-radius:12px 12px 0 0;font-family:"PT Sans Narrow",sans-serif;font-size:18px;color:#fff}
.nav-item{position:absolute;top:19px;display:flex;align-items:center;gap:8px}
.nav-item .caret{width:0;height:0;border-left:6px solid transparent;border-right:6px solid transparent;border-top:6px solid #888}
.hero{position:absolute;left:3px;top:164px;width:1003px;height:427px;background:radial-gradient(ellipse at 70% 50%,#c8893a,#7a4a18 55%,#3a200a)}
.hero-bar{position:absolute;left:3px;top:590px;width:1003px;height:40px;background:var(--green);border-radius:0 0 12px 12px}
.hero-title{position:absolute;left:27px;top:4px;font-family:"PT Sans Narrow",sans-serif;font-size:27px;color:#fff}
.btn{position:absolute;background:linear-gradient(#fff,#d9d9d9);border:1px solid #bbb;border-radius:10px;font-size:17px;color:#111;display:flex;align-items:center;justify-content:center;box-shadow:0 1px 2px rgba(0,0,0,.3)}
.hero-bar .btn{left:845px;top:5px;width:146px;height:34px}
.card{position:absolute;top:651px;width:318px;height:150px;border-radius:6px;color:#fff;font-family:"PT Sans Narrow",sans-serif}
.card-blue{left:3px;background:linear-gradient(135deg,#4f87cc,var(--blue))}
.card-green{left:346px;background:linear-gradient(135deg,#9fcb4a,var(--green-dark))}
.card-orange{left:687px;width:317px;background:linear-gradient(135deg,#ffc84a,#f7a30f)}
.card-art{position:absolute;left:16px;top:14px;width:84px;height:112px;border-radius:40px;opacity:.85}
.card-title{position:absolute;left:118px;top:20px;font-size:28px;line-height:29px}
.card-sub{position:absolute;left:118px;font-size:17px;color:#f3f3f3}
.go{position:absolute;right:14px;bottom:14px;width:50px;height:22px;border-radius:11px;font-size:16px;display:flex;align-items:center;justify-content:center;color:#fff}
.welcome-title{position:absolute;left:7px;top:830px;font-family:"PT Sans Narrow",sans-serif;font-weight:700;font-size:29px;line-height:1}
.welcome-art{position:absolute;left:3px;top:868px;width:216px;height:206px;border-radius:6px;background:linear-gradient(135deg,#e9d8c6,#b87845 60%,#7a4a2a)}
.welcome-text{position:absolute;left:243px;top:866px;width:412px;font-size:13.5px;line-height:24px;text-align:justify}
.welcome-btn{left:512px;top:1040px;width:144px;height:37px}
.ad-box{position:absolute;left:687px;top:826px;width:317px;height:251px;background:var(--grey-panel);border-radius:6px;color:#fff;font-size:13.5px;line-height:24px;display:flex;align-items:center;justify-content:center;text-align:center}
.footer{position:absolute;left:0;top:1111px;width:1011px;height:89px;background:var(--footer);color:#fff;text-align:center}
.footer-links{margin-top:25px;font-size:12px}
.footer-copy{margin-top:12px;font-size:12px}
</style>
</head>
<body>
<header>
  <div class="brand"><span class="brand-mark"></span><span class="brand-name">Heralds of Grace</span></div>
  <div class="tagline">Living Out Our Calling Together</div>
  <div class="search"><div class="search-field"></div><div class="search-btn">SEARCH</div></div>
</header>
<nav class="nav">
  <span class="nav-item" style="left:34px">Home</span>
  <span class="nav-item" style="left:134px">About Us <i class="caret"></i></span>
  <span class="nav-item" style="left:247px">Membership <i class="caret"></i></span>
  <span class="nav-item" style="left:381px">Member Projects <i class="caret"></i></span>
  <span class="nav-item" style="left:540px">Membership Levels <i class="caret"></i></span>
  <span class="nav-item" style="left:714px">Links <i class="caret"></i></span>
  <span class="nav-item" style="left:810px">Contact us <i class="caret"></i></span>
  <span class="nav-item" style="left:931px">Login <i class="caret"></i></span>
</nav>
<section>
  <div class="hero" role="img" aria-label="Photo of praying hands in front of a weathered cross in warm sepia tones"></div>
  <div class="hero-bar"><div class="hero-title">WELCOME TO 2012 COMPLIMENTS</div><div class="btn">READ MORE</div></div>
</section>
<section>
  <div class="card card-blue">
    <div class="card-art" role="img" aria-label="Illustration of a glowing light bulb" style="background:radial-gradient(#fff8a0,#f2c300)"></div>
    <div class="card-title">OUR OBJECTIVES</div>
    <div class="card-sub" style="top:58px">Who We Are &nbsp;|&nbsp; What We Do</div>
    <div class="go" style="background:#6aa6e6">GO ›</div>
  </div>
  <div class="card card-green">
    <div class="card-art" role="img" aria-label="Illustration of a document organiser icon" style="top:26px;height:76px;border-radius:8px;background:linear-gradient(#e9c98a,#a97a2e)"></div>
    <div class="card-title" style="left:106px;font-size:25px">MEMBERSHIP LEVELS<br>/ BENEFITS</div>
    <div class="card-sub" style="left:106px;top:88px;font-size:15px">Associate &nbsp;|&nbsp; Gold &nbsp;|&nbsp; Silver &nbsp;|&nbsp; Premium</div>
    <div class="go" style="background:#8fe01c">GO ›</div>
  </div>
  <div class="card card-orange">
    <div class="card-art" role="img" aria-label="Illustration of a registration form with a pen" style="border-radius:4px;background:linear-gradient(#ffffff,#e4e4e4)"></div>
    <div class="card-title" style="left:126px">REGISTRATION</div>
    <div class="card-sub" style="left:126px;top:58px;line-height:21px">Join the heralds of grace int'l<br>fellowship</div>
    <div class="go" style="background:#c98a05">GO ›</div>
  </div>
</section>
<main>
  <h1 class="welcome-title">WELCOME</h1>
  <div class="welcome-art" role="img" aria-label="Photo of a hand stacking coins with the words Learn the saving culture"></div>
  <p class="welcome-text">Heralds of Grace International Fellowship (QRTV) was established on the 19th day of July 2008 by a group of Christian men from various Church denominations. QRTV is an interdenominational and non-denominational fellowship, born out of a great and overwhelming burden for our generation and a strong desire to see the kingdom of God come and His will be done on Earth as it is in Heaven...</p>
  <div class="btn welcome-btn">READ MORE</div>
  <aside class="ad-box">Members Business / Products<br>Advertisement Comes here</aside>
</main>
<footer class="footer">
  <div class="footer-links">HOME &nbsp;| &nbsp;ABOUT US &nbsp;| &nbsp;BENEFITS &nbsp;| &nbsp;HERALDS OF GRACE &nbsp;| &nbsp;SMS &nbsp;| &nbsp;CONSTRUCTION COMPANY &nbsp;| &nbsp;MEMBERSHIP LEVELS &nbsp;| &nbsp;LOGIN &nbsp;| &nbsp;CONTACT US</div>
  <div class="footer-copy">Heralds of Grace International Fellowship. © 2012. All rights reserved.</div>
</footer>
</body>
</html>
```